Harborline Auto LLC

Car Dealer Customer Service
Address: 2874 Cresthaven Road, Shelbyville, TN 37162
web: www.harborlineautoxq.net
email: harborlineautoxq@mailnest.example
Phone: (931) 555-0148
Phone: (629) 555-0173

```html
<!DOCTYPE html>
<html lang="en">
<head>
<meta charset="utf-8">
<title>Harborline Auto – Business Card</title>
<link rel="stylesheet" href="https://fonts.googleapis.com/css2?family=Lexend:wght@600&family=Poppins:ital,wght@0,400;0,600;1,400&display=swap">
<style>
  :root {
    --stage: #232323;
    --card-white: #f1f1f1;
    --brand-blue: #2180bf;
    --deep-blue: #155f8e;
    --blue-dark: #125a88;
    --blue-light: #2487c2;
    --gold: #e0a93a;
    --ink: #1e1e1e;
    --white: #ffffff;
  }
  html, body {
    margin: 0;
    padding: 0;
    width: 1200px;
    height: 576px;
    overflow: hidden;
    background: var(--stage);
  }
  .canvas {
    position: relative;
    width: 1200px;
    height: 576px;
  }
  .card {
    position: absolute;
    top: 138px;
    width: 484px;
    height: 293px;
    border-radius: 10px;
    overflow: hidden;
  }
  .card-front {
    left: 102px;
    background: var(--card-white);
  }
  .card-back {
    left: 596px;
    background: linear-gradient(160deg, var(--blue-dark) 0%, var(--blue-light) 100%);
  }
  .brand-name {
    margin: 0;
    font-family: "Lexend", sans-serif;
    font-weight: 600;
    font-size: 29px;
    letter-spacing: 0.5px;
    line-height: 1;
    text-transform: uppercase;
  }
  .card-front .brand-name {
    position: absolute;
    left: 46px;
    top: 36px;
    color: var(--brand-blue);
  }
  .card-back .brand-name {
    position: absolute;
    right: 26px;
    top: 228px;
    color: var(--white);
  }
  .brand-circle {
    position: absolute;
    width: 280px;
    height: 280px;
    border-radius: 50%;
    top: 6px;
  }
  .card-front .brand-circle {
    left: 354px;
    background: var(--brand-blue);
  }
  .card-back .brand-circle {
    left: -140px;
    background: var(--white);
  }
  .role {
    position: absolute;
    left: 26px;
    top: 105px;
    margin: 0;
    font-family: "Poppins", sans-serif;
    font-style: italic;
    font-size: 13px;
    color: var(--ink);
  }
  .phones {
    position: absolute;
    left: 26px;
    top: 126px;
    margin: 0;
    padding: 0;
    list-style: none;
  }
  .phones li {
    display: flex;
    align-items: center;
    gap: 8px;
    height: 23px;
    font-family: "Poppins", sans-serif;
    font-weight: 600;
    font-size: 16.5px;
    color: var(--deep-blue);
  }
  .phones svg { width: 15px; height: 15px; fill: var(--gold); }
  .contact {
    position: absolute;
    left: 26px;
    top: 210px;
    margin: 0;
    padding: 0;
    list-style: none;
    font-family: "Poppins", sans-serif;
    font-size: 12.5px;
    color: var(--ink);
  }
  .contact li {
    display: flex;
    align-items: center;
    gap: 8px;
    height: 17px;
  }
  .contact li.address { margin-top: 5px; }
  .contact svg { width: 10px; height: 10px; fill: var(--gold); stroke: var(--gold); }
</style>
</head>
<body>
<main class="canvas">
  <section class="card card-front">
    <div class="brand-circle"></div>
    <h1 class="brand-name">Harborline Auto</h1>
    <p class="role">Car Dealer Customer Service</p>
    <ul class="phones">
      <li>
        <svg viewBox="0 0 24 24" aria-hidden="true"><path d="M6.6 10.8a15.2 15.2 0 0 0 6.6 6.6l2.2-2.2c.3-.3.7-.4 1-.2 1.1.4 2.3.6 3.6.6.6 0 1 .4 1 1V20c0 .6-.4 1-1 1A17 17 0 0 1 3 4c0-.6.4-1 1-1h3.5c.6 0 1 .4 1 1 0 1.3.2 2.5.6 3.6.1.3 0 .7-.2 1z"/></svg>
        931-555-0148
      </li>
      <li>
        <svg viewBox="0 0 24 24" aria-hidden="true"><path d="M6.6 10.8a15.2 15.2 0 0 0 6.6 6.6l2.2-2.2c.3-.3.7-.4 1-.2 1.1.4 2.3.6 3.6.6.6 0 1 .4 1 1V20c0 .6-.4 1-1 1A17 17 0 0 1 3 4c0-.6.4-1 1-1h3.5c.6 0 1 .4 1 1 0 1.3.2 2.5.6 3.6.1.3 0 .7-.2 1z"/></svg>
        629-555-0173
      </li>
    </ul>
    <ul class="contact">
      <li>
        <svg viewBox="0 0 12 12" aria-hidden="true"><rect x="0.5" y="2" width="11" height="8" stroke="none"/><path d="M0.5 2.5 6 6.5 11.5 2.5" fill="none" stroke="#f1f1f1" stroke-width="1"/></svg>
        www.harborlineautoxq.net
      </li>
      <li>
        <svg viewBox="0 0 12 12" aria-hidden="true"><circle cx="6" cy="6" r="5" fill="none" stroke-width="1.3"/><path d="M1 6h10M6 1c-2.4 2.8-2.4 7.2 0 10M6 1c2.4 2.8 2.4 7.2 0 10" fill="none" stroke-width="1"/></svg>
        harborlineautoxq@mailnest.example
      </li>
      <li class="address">2874 Cresthaven Road, Shelbyville, TN 37162</li>
    </ul>
  </section>
  <section class="card card-back">
    <div class="brand-circle"></div>
    <p class="brand-name">Harborline Auto</p>
  </section>
</main>
</body>
</html>
```